Buch-/E-Book-Cover für Kinderbuch zum spielerischen Umgang zwischen Kind und Hund
Zielgruppe
Die Zielgruppe sind Kinder die lernen möchten mit Ihrem Hund besser zu spielen, verstehen und erziehen. Es ist ein Kinderbuch und das Buch soll dementsprechend 'kinderlicher' gestaltet sein.
Ich habe kein eigenes Konzept für das Cover mir derzeitig überlegt und ich werde die erstellten Cover bei meiner Zielgruppe testen und danach den Gewinner küren.
In diesem Buch handelt sich um ein Sachbuch zum Thema Hundeerziehung für Kinder. Ich möchte Ihnen die Inhaltsangabe, Vorwort und Buchrückseite mitteilen. Das Buch werde ich auf Lesekorb.de veröffentlichen. Außerdem möchte ich Ihnen die 2 größten Konkurrenten vorstellen.
Das Vorwort:
Vorwort
Der Hund ist für das Kind mehr als nur ein vierbeiniger Hausgenosse mit Kuschelfaktor, er ist ein echter Partner zum Spielen und Lernen. Mit den passenden Ideen gestaltet sich der Alltag mit dem Tier richtig spannend. Sowohl Kind als auch Hund entwickeln sich Schritt für Schritt weiter und wachsen immer mehr zusammen. Für Jungen und Mädchen gibt es vielfältige Möglichkeiten, sich mit ihrem Vierbeiner zu beschäftigen. Kreative Rollenspiele gehören ebenso dazu wie das Lernen von Kunststücken, das Training von Intelligenz und Geschicklichkeit und das Basteln schöner Spielsachen. Lassen Sie sich von diesem Buch inspirieren und von den Fähigkeiten Ihrer Kinder und Hunde überraschen!
Gliederung:
Einleitung und Grundlegendes
1. Warum spielen Hunde und Kinder?
Gemeinsamkeiten zwischen Kind und Welpe
Die Vorteile einer engen Hund-Kind-Beziehung
Kind und Hund – das absolute Dream-Team?
Welcher Hund passt zum Kind?
Voraussetzungen für sicheres Spielen
2. Kreative Spiele
Kreative Beschäftigung mit dem Hund – darf das sein?
Rollenspiele mit Hunden
Das richtige Alter für Rollenspiele
Beispiele für typische Rollenspiele im Kindesalter
Tierische Rollenspiele – vom Kind zum Hund
Eigene Kommandos erfi..
Aufgabenstellung
Der Titel vom Buch lautet: Komm zu uns! Wo Kleine den Vierbeiner kennen, führen und mit ihm toben dürfen.
Das sind die 2 größten Konkurrenten https://www.lesekorb.example/titel/4718
https://www.lesekorb.example/titel/5923
Das sind Cover auf dem Englisch sprachigen Markt die ich sehr gut finde
1. https://www.readbasket.example/item/8841
2. https://www.readbasket.example/item/3307

```html
<!DOCTYPE html>
<html lang="de">
<head>
<meta charset="utf-8">
<title>Komm zu uns! – Cover und Buchtexte</title>
<link rel="stylesheet" href="https://fonts.googleapis.com/css2?family=Pacifico&family=Sniglet:wght@400;800&family=Indie+Flower&display=swap">
<style>
  :root{
    --cream:#fffcd6;
    --cream-deep:#fbf1c4;
    --brown:#8f4519;
    --brown-text:#8a4a2a;
    --title-shadow:#f3d67a;
    --bubble:#f1d384;
    --heading-fill:#c99378;
    --heading-line:#8a4a2a;
    --art-warm:#d9a77a;
    --art-soft:#e8c69a;
    --art-kids:#e9b98f;
  }
  *{box-sizing:border-box;margin:0;padding:0}
  html,body{width:1200px;height:960px;overflow:hidden;background:var(--cream)}
  .spread{position:relative;width:1200px;height:960px;overflow:hidden}
  .backdrop{position:absolute;inset:0;background:radial-gradient(circle at 30% 30%,var(--cream) 0%,var(--cream-deep) 100%)}
  .panel{position:absolute;top:0;width:600px;height:960px}
  .panel--front{left:0}
  .panel--info{left:600px}
  .art{position:absolute;border-radius:40px}
  .art--puppy{left:326px;top:40px;width:226px;height:163px;background:linear-gradient(135deg,var(--art-soft),var(--art-warm))}
  .art--child-dog{left:92px;top:340px;width:412px;height:331px;background:linear-gradient(160deg,var(--art-soft),var(--art-warm));border-radius:50%}
  .title{position:absolute;left:0;top:40px;width:600px;font-family:"Pacifico",cursive;color:var(--brown);text-shadow:4px 5px 0 var(--title-shadow);line-height:1}
  .title__line{position:absolute;white-space:nowrap}
  .title__line--one{left:38px;top:12px;font-size:96px}
  .title__line--two{left:24px;top:150px;font-size:96px}
  .subtitle{position:absolute;left:20px;top:688px;width:560px;text-align:center;font-family:"Sniglet",sans-serif;font-weight:800;font-size:37px;line-height:62px;color:var(--brown);text-shadow:2px 3px 4px rgba(143,69,25,.35)}
  .heading{position:absolute;font-family:"Sniglet",sans-serif;font-weight:800;color:var(--heading-fill);-webkit-text-stroke:1.5px var(--heading-line);text-shadow:2px 2px 0 #fff;z-index:2}
  .heading--foreword{left:68px;top:60px;font-size:42px}
  .heading--back{left:42px;top:428px;font-size:40px}
  .bubble{position:absolute;left:0;top:0;width:600px;height:960px}
  .bubble__text{position:absolute;text-align:center;color:var(--brown-text)}
  .bubble__text--foreword{left:50px;top:112px;width:530px;font-family:"Indie Flower",cursive;font-size:15.5px;line-height:22.8px}
  .bubble__text--back{left:40px;top:477px;width:540px;font-family:"Sniglet",sans-serif;font-weight:800;font-size:13.6px;line-height:20.7px}
  .art--kid-left{left:18px;top:738px;width:235px;height:210px;background:linear-gradient(160deg,var(--art-kids),var(--art-warm))}
  .art--kid-right{left:352px;top:735px;width:232px;height:212px;background:linear-gradient(160deg,var(--art-kids),var(--art-warm))}
</style>
</head>
<body>
<main class="spread">
  <div class="backdrop" role="img" aria-label="Hintergrundmuster aus bunten Tupfen und Knochen in Grün, Orange, Gelb und Hellblau"></div>

  <section class="panel panel--front">
    <div class="art art--puppy" role="img" aria-label="Illustration: springender brauner Welpe"></div>
    <h1 class="title">
      <span class="title__line title__line--one">Komm</span>
      <span class="title__line title__line--two">zu uns!</span>
    </h1>
    <div class="art art--child-dog" role="img" aria-label="Illustration: kleines Kind liegt auf einem großen braunen Hund"></div>
    <p class="subtitle">Wo Kleine den Vierbeiner kennen, führen und mit ihm toben dürfen</p>
  </section>

  <section class="panel panel--info">
    <svg class="bubble" viewBox="0 0 600 960" aria-hidden="true">
      <path fill="var(--bubble)" d="M60 95 H560 Q586 95 586 125 V330 Q586 367 550 367 H160 Q150 400 172 440 Q130 410 120 367 H50 Q15 367 15 330 V130 Q15 95 60 95 Z"/>
      <path fill="var(--bubble)" d="M62 462 H555 Q586 462 586 495 V695 Q586 730 550 730 H484 Q478 770 486 802 Q455 770 446 730 H60 Q24 730 24 695 V495 Q24 462 62 462 Z"/>
    </svg>
    <h2 class="heading heading--foreword">Vorwort</h2>
    <p class="bubble__text bubble__text--foreword">Der Hund ist für das Kind mehr als nur ein vierbeiniger Hausgenosse mit Kuschelfaktor, er ist ein echter Partner zum Spielen und Lernen. Mit den passenden Ideen gestaltet sich der Alltag mit dem Tier richtig spannend. Sowohl Kind als auch Hund entwickeln sich Schritt für Schritt weiter und wachsen immer mehr zusammen. Für Jungen und Mädchen gibt es vielfältige Möglichkeiten, sich mit ihrem Vierbeiner zu beschäftigen. Kreative Rollenspiele gehören ebenso dazu wie das Lernen von Kunststücken, das Training von Intelligenz und Geschicklichkeit und das Basteln schöner Spielsachen. Lassen Sie sich von diesem Buch inspirieren und von den Fähigkeiten Ihrer Kinder und Hunde überraschen!</p>

    <h2 class="heading heading--back">Buchrückseite</h2>
    <p class="bubble__text bubble__text--back">Beim Spielen lernen Hunde und Kinder gemeinsam. Sie trainieren ihre Geschicklichkeit, Intelligenz und soziale Kompetenz. Die Beschäftigung mit dem Hund fördert aber auch die Kreativität und bietet zahlreiche Anreize zum Basteln und Werken. Lustige Spiele mit dem Tier sorgen schon bei ganz kleinen Kindern für tolle Erfolgserlebnisse und viele heitere Momente. Im Urlaub, am Strand, im Schnee, zu Hause oder in der freien Natur gibt es die tollsten Spielmöglichkeiten. Die spannenden Abenteuer schweißen das Kind-Hund-Team zusammen und bereiten es auf eine großartige Zukunft vor. Im Schulalter absolvieren die kleinen Hundehalter ihre ersten Agility-Übungen und bringen ihren Tieren knifflige Tricks bei. Krönender Abschluss: der Hundeführerschein.</p>

    <div class="art art--kid-left" role="img" aria-label="Illustration: Mädchen mit Zöpfen führt einen kleinen Hund an der Leine"></div>
    <div class="art art--kid-right" role="img" aria-label="Illustration: Mädchen im gestreiften Kleid führt einen kleinen Hund an der Leine"></div>
  </section>
</main>
</body>
</html>
```